Animal Eye Clinic needs a Business card

We are a new veterinary ophthalmology practice (Ridgeline Pet Vision Care) and we need a business card designed. We only see animal eyes - we are not a regular veterinary clinic. We already have a logo. We are looking for a professional, good looking business card to hand out to our clients. We are looking for something simple but professional and contemporary. Our logo is likely the only picture/graphic that needs to be on the card.
Updates

Contact Information for Business Card

Delia Vossman, BSc, DVM, MSc, DipACVO
Veterinary Ophthalmologist

Phone: 250.418.3927
Email: ridgelinepetvisioncare@mailbox-example.net
Website: ridgelinepetvisioncare-example.net
Address: 1874 Thornbury Rd
Kelowna, BC, V1X 4M9

Colors

Designer to choose colors to be used in the design.

Requirements
Must have
• Our logo (attached)

```html
<!DOCTYPE html>
<html lang="en">
<head>
<meta charset="utf-8">
<title>Ridgeline Pet Vision Care – Business Card</title>
<link href="https://fonts.googleapis.com/css2?family=Open+Sans:wght@400;700&family=Roboto+Condensed:wght@400&display=swap" rel="stylesheet">
<style>
  :root {
    --teal: #0597a9;
    --teal-dark: #047e8d;
    --grey: #6f7173;
    --ink: #4a4c4e;
    --rule: #9a9c9e;
    --paper: #ffffff;
    --backdrop: #d9dadb;
  }
  * { box-sizing: border-box; margin: 0; padding: 0; }
  html, body {
    width: 1200px; height: 800px; overflow: hidden;
    background: var(--backdrop);
    font-family: "Open Sans", Arial, sans-serif;
  }
  .stage { position: relative; width: 1200px; height: 800px; }
  .card {
    position: absolute; top: 245px;
    width: 540px; height: 309px;
    background: var(--paper);
    box-shadow: 0 10px 28px rgba(0,0,0,.18);
    overflow: hidden;
  }
  .card--front { left: 40px; border-bottom: 4px solid var(--teal); }
  .card--back { left: 620px; }

  /* Front */
  .brand {
    position: absolute; top: 34px; right: 34px;
    display: flex; align-items: center; gap: 10px;
    color: var(--teal); font-weight: 700; font-size: 17px;
    text-transform: uppercase; letter-spacing: .3px;
  }
  .brand__dot { width: 18px; height: 18px; border-radius: 50%; background: var(--teal); }
  .person { position: absolute; left: 34px; top: 128px; }
  .person__name {
    color: var(--teal); font-weight: 700; font-size: 16px; text-transform: uppercase;
  }
  .person__creds {
    font-family: "Roboto Condensed", Arial, sans-serif; font-weight: 400;
    font-size: 12px; text-transform: none;
  }
  .person__title { color: var(--grey); font-size: 12.5px; margin-top: 1px; }
  .contact { list-style: none; margin-top: 10px; }
  .contact li {
    display: flex; align-items: center; gap: 8px;
    color: var(--ink); font-size: 12.5px; line-height: 19px;
  }
  .contact svg { width: 11px; height: 11px; flex: none; fill: var(--teal); }
  .divider {
    position: absolute; left: 34px; right: 34px; top: 262px;
    border-top: 1px solid var(--rule);
  }
  .address {
    position: absolute; left: 34px; top: 271px;
    display: flex; align-items: center; gap: 8px;
    color: var(--ink); font-size: 12.5px;
  }
  .address svg { width: 11px; height: 12px; fill: var(--teal); }

  /* Back */
  .back-art {
    position: absolute; left: 0; top: 0; bottom: 0; width: 290px;
    background: linear-gradient(135deg, var(--teal) 0%, var(--teal-dark) 70%, #7d7f81 100%);
  }
  .back-text {
    position: absolute; left: 320px; right: 24px; top: 0; bottom: 0;
    display: flex; flex-direction: column; justify-content: center; gap: 12px;
  }
  .back-text__name {
    color: var(--teal); font-weight: 700; font-size: 22px; line-height: 1.15;
    text-transform: uppercase;
  }
  .back-text__web {
    color: var(--grey); font-size: 10.5px; text-transform: uppercase; letter-spacing: .3px;
  }
</style>
</head>
<body>
<main class="stage">

  <section class="card card--front" aria-label="Business card front">
    <div class="brand"><span class="brand__dot"></span>Ridgeline Pet Vision Care</div>

    <div class="person">
      <p class="person__name">Delia Vossman, <span class="person__creds">BSc, DVM, MSc, DipACVO</span></p>
      <p class="person__title">Veterinary Ophthalmologist</p>
      <ul class="contact">
        <li>
          <svg viewBox="0 0 24 24"><path d="M6.6 10.8a15.1 15.1 0 0 0 6.6 6.6l2.2-2.2c.3-.3.7-.4 1-.2 1.1.4 2.3.6 3.6.6.6 0 1 .4 1 1V20c0 .6-.4 1-1 1A17 17 0 0 1 3 4c0-.6.4-1 1-1h3.5c.6 0 1 .4 1 1 0 1.3.2 2.5.6 3.6.1.3 0 .7-.2 1z"/></svg>
          250.418.3927
        </li>
        <li>
          <svg viewBox="0 0 24 24"><path d="M2 5h20v14H2zm2 2v.5l8 5 8-5V7l-8 5z"/></svg>
          ridgelinepetvisioncare@mailbox-example.net
        </li>
        <li>
          <svg viewBox="0 0 24 24"><path d="M12 2a10 10 0 1 0 0 20 10 10 0 0 0 0-20zm6.9 6h-3a15 15 0 0 0-1.3-3.9A8 8 0 0 1 18.9 8zM12 4c.8 1.2 1.5 2.5 1.9 4h-3.8c.4-1.5 1.1-2.8 1.9-4zM4.3 14a8 8 0 0 1 0-4h3.4a16 16 0 0 0 0 4zm.8 2h3a15 15 0 0 0 1.3 3.9A8 8 0 0 1 5.1 16zM8 8H5.1a8 8 0 0 1 4.3-3.9C8.8 5.2 8.4 6.6 8 8zm4 12c-.8-1.2-1.5-2.5-1.9-4h3.8c-.4 1.5-1.1 2.8-1.9 4zm2.3-6H9.7a14 14 0 0 1 0-4h4.6a14 14 0 0 1 0 4zm.3 5.9c.6-1.2 1-2.5 1.3-3.9h3a8 8 0 0 1-4.3 3.9zm1.7-5.9a16 16 0 0 0 0-4h3.4a8 8 0 0 1 0 4z"/></svg>
          ridgelinepetvisioncare-example.net
        </li>
      </ul>
    </div>

    <div class="divider"></div>
    <p class="address">
      <svg viewBox="0 0 24 26"><path d="M12 1a8 8 0 0 0-8 8c0 6 8 15 8 15s8-9 8-15a8 8 0 0 0-8-8zm0 11a3 3 0 1 1 0-6 3 3 0 0 1 0 6z"/></svg>
      1874 Thornbury Rd Kelowna, BC, V1X 4M9
    </p>
  </section>

  <section class="card card--back" aria-label="Business card back">
    <div class="back-art" role="img" aria-label="Large brand illustration of a horse, dog and cat in teal and grey"></div>
    <div class="back-text">
      <p class="back-text__name">Ridgeline Pet Vision Care</p>
      <p class="back-text__web">www.ridgelinepetvisioncare-example.net</p>
    </div>
  </section>

</main>
</body>
</html>
```